Landscape design build company door flyer

I would like this flyer to convey a high-level of professionalism for a company that is excellent with communication with their clients as well as a company that does incredible installations

Went on vacation/holiday

```html
<!DOCTYPE html>
<html lang="en">
<head>
<meta charset="utf-8">
<title>Summit Stone Builders – Outdoor Living Flyer</title>
<link rel="stylesheet" href="https://fonts.googleapis.com/css2?family=Poppins:wght@400;500;600;700;800&family=Oswald:wght@500;600;700&display=swap">
<style>
  :root {
    --navy: #15304a;
    --gold: #f6b100;
    --paper: #f1f1f1;
    --ink: #1f2328;
    --white: #ffffff;
    --stage: #e6e6e6;
  }
  * { box-sizing: border-box; margin: 0; padding: 0; }
  html, body { width: 1200px; height: 1029px; overflow: hidden; background: var(--stage); }
  .flyer {
    position: absolute; left: 219px; top: 24px;
    width: 761px; height: 980px;
    background: var(--paper);
    border: 1px solid #5a5a5a;
    overflow: hidden;
    font-family: "Poppins", sans-serif;
    color: var(--ink);
  }
  .hero-photo {
    position: absolute; left: 0; top: 0; width: 100%; height: 533px;
    background:
      radial-gradient(ellipse at 85% 10%, #7fb6de 0%, rgba(127,182,222,0) 45%),
      radial-gradient(ellipse at 8% 45%, #4d6b3c 0%, rgba(77,107,60,0) 40%),
      radial-gradient(ellipse at 92% 60%, #3f5a3a 0%, rgba(63,90,58,0) 35%),
      linear-gradient(180deg, #4f7ea8 0%, #39506a 35%, #30404f 60%, #2c3d52 100%);
  }
  .brand-panel {
    position: absolute; left: 0; top: 0; width: 436px; height: 166px;
  }
  .brand-name {
    position: absolute; left: 0; width: 370px; top: 106px; text-align: center;
    font-family: "Poppins", sans-serif; font-weight: 700; font-size: 20px;
    color: var(--navy); letter-spacing: 0.2px; line-height: 1;
  }
  .brand-mark {
    position: absolute; left: 163px; top: 40px; width: 44px; height: 44px;
    background: var(--navy);
  }
  .brand-tagline {
    position: absolute; left: 0; width: 370px; top: 131px; text-align: center;
    font-weight: 500; font-size: 10px; color: var(--navy); letter-spacing: 0.2px;
  }
  .headline {
    position: absolute; left: 76px; top: 216px;
    font-weight: 800; font-size: 50px; line-height: 44px;
    letter-spacing: -1.5px; color: var(--white); text-transform: uppercase;
  }
  .headline .accent { color: var(--gold); }
  .showcase {
    position: absolute; top: 412px; width: 196px; height: 196px;
    border-radius: 50%; border: 5px solid var(--white);
  }
  .showcase.fireplace { left: 48px;
    background: linear-gradient(160deg, #8a8d92 0%, #5d6168 45%, #3a3e45 100%); }
  .showcase.walkway { left: 283px;
    background: linear-gradient(100deg, #4f8d2e 0%, #6fa844 22%, #cfcac0 40%, #bdb6aa 75%, #5f6a4a 100%); }
  .showcase.firepit { left: 518px;
    background: radial-gradient(circle at 65% 25%, #3f8fa6 0%, rgba(63,143,166,0) 30%),
                linear-gradient(180deg, #4a5a3e 0%, #6b5548 40%, #5a463e 75%, #3b2f2b 100%); }
  .section-title {
    position: absolute; top: 650px;
    font-weight: 600; font-size: 23px; color: var(--navy); letter-spacing: 0.2px;
  }
  .about-title { left: 33px; }
  .services-title { left: 449px; }
  .about-copy {
    position: absolute; left: 33px; top: 696px; width: 323px;
    font-size: 11.6px; line-height: 14.6px; text-align: justify; color: var(--ink);
  }
  .about-copy p + p { margin-top: 14px; font-weight: 500; }
  .divider {
    position: absolute; left: 403px; top: 681px; width: 2px; height: 165px;
    background: var(--navy); border-radius: 1px;
  }
  .service-list {
    position: absolute; left: 449px; top: 689px; list-style: none;
  }
  .service-list li {
    display: flex; align-items: center; height: 25.5px;
    font-weight: 500; font-size: 16px; color: var(--ink);
  }
  .service-list svg { width: 16px; height: 16px; margin-right: 18px; flex: none; }
  .contact-title {
    position: absolute; left: 33px; top: 912px;
    font-weight: 700; font-size: 26px; letter-spacing: 2px; color: var(--gold); line-height: 1;
  }
  .contact-links {
    position: absolute; left: 33px; top: 944px; display: flex; gap: 30px;
    font-family: "Oswald", sans-serif; font-weight: 500; font-size: 11px; color: var(--navy);
  }
  .contact-links span { display: flex; align-items: center; gap: 5px; }
  .contact-links svg { width: 11px; height: 11px; }
  .estimate-band {
    position: absolute; left: 362px; top: 909px; width: 399px; height: 55px;
    background: var(--navy); display: flex; align-items: center; padding-left: 12px;
  }
  .estimate-band .phone-icon { width: 22px; height: 22px; flex: none; }
  .estimate-band .phone {
    margin-left: 11px; font-family: "Oswald", sans-serif; font-weight: 700;
    font-size: 31px; color: var(--gold); letter-spacing: 0.5px;
  }
  .estimate-band .cta {
    margin-left: 10px; font-family: "Oswald", sans-serif; font-weight: 600;
    font-size: 17px; color: var(--white); letter-spacing: -0.3px;
  }
</style>
</head>
<body>
<main class="flyer">
  <div class="hero-photo" role="img" aria-label="Photo of a covered backyard pavilion with stone outdoor kitchen, paver patio and trees under a blue sky"></div>

  <svg class="brand-panel" viewBox="0 0 436 166" aria-hidden="true">
    <polygon points="0,0 436,0 351,166 0,166" fill="#f1f1f1"/>
  </svg>
  <div class="brand-mark" aria-hidden="true"></div>
  <div class="brand-name">SUMMIT STONE BUILDERS</div>
  <div class="brand-tagline">OUTDOOR LIVING SPACES</div>

  <h1 class="headline">
    Let’s Create<br>
    Your Dream<br>
    <span class="accent">Outdoor Living Space!</span>
  </h1>

  <div class="showcase fireplace" role="img" aria-label="Photo of a stacked stone outdoor fireplace"></div>
  <div class="showcase walkway" role="img" aria-label="Photo of a curved paver walkway beside a lawn"></div>
  <div class="showcase firepit" role="img" aria-label="Photo of a lit paver patio with fire pit and pool"></div>

  <h2 class="section-title about-title">ABOUT US</h2>
  <div class="about-copy">
    <p>Discover the endless possibilities for your outdoor space with The Summit Stone Team. Our team of skilled artisans is dedicated to turning your outdoor space into a breathtaking oasis that you’ll love coming home to. Whether it’s a cozy patio for intimate gatherings, a sprawling deck to host memorable parties, or a custom paver driveway that adds instant curb appeal, our high-quality craftsmanship ensures stunning results that exceed your expectations.</p>
    <p>Our service areas include Bellevue, Issaquah, Kirkland, Redmond, Sammamish.</p>
  </div>

  <div class="divider"></div>

  <h2 class="section-title services-title">OUR SERVICES</h2>
  <ul class="service-list">
    <li><svg viewBox="0 0 16 16"><circle cx="8" cy="8" r="8" fill="#15304a"/><path d="M4.5 8.3l2.4 2.3 4.6-4.8" fill="none" stroke="#fff" stroke-width="1.9" stroke-linecap="round" stroke-linejoin="round"/></svg>Paver Patios</li>
    <li><svg viewBox="0 0 16 16"><circle cx="8" cy="8" r="8" fill="#15304a"/><path d="M4.5 8.3l2.4 2.3 4.6-4.8" fill="none" stroke="#fff" stroke-width="1.9" stroke-linecap="round" stroke-linejoin="round"/></svg>Paver Driveways</li>
    <li><svg viewBox="0 0 16 16"><circle cx="8" cy="8" r="8" fill="#15304a"/><path d="M4.5 8.3l2.4 2.3 4.6-4.8" fill="none" stroke="#fff" stroke-width="1.9" stroke-linecap="round" stroke-linejoin="round"/></svg>Retaining Walls</li>
    <li><svg viewBox="0 0 16 16"><circle cx="8" cy="8" r="8" fill="#15304a"/><path d="M4.5 8.3l2.4 2.3 4.6-4.8" fill="none" stroke="#fff" stroke-width="1.9" stroke-linecap="round" stroke-linejoin="round"/></svg>Decks &amp; Railings</li>
    <li><svg viewBox="0 0 16 16"><circle cx="8" cy="8" r="8" fill="#15304a"/><path d="M4.5 8.3l2.4 2.3 4.6-4.8" fill="none" stroke="#fff" stroke-width="1.9" stroke-linecap="round" stroke-linejoin="round"/></svg>Pools</li>
    <li><svg viewBox="0 0 16 16"><circle cx="8" cy="8" r="8" fill="#15304a"/><path d="M4.5 8.3l2.4 2.3 4.6-4.8" fill="none" stroke="#fff" stroke-width="1.9" stroke-linecap="round" stroke-linejoin="round"/></svg>Outdoor Lighting</li>
    <li><svg viewBox="0 0 16 16"><circle cx="8" cy="8" r="8" fill="#15304a"/><path d="M4.5 8.3l2.4 2.3 4.6-4.8" fill="none" stroke="#fff" stroke-width="1.9" stroke-linecap="round" stroke-linejoin="round"/></svg>Firepits &amp; Fireplaces</li>
  </ul>

  <div class="contact-title">CONTACT US TODAY!</div>
  <div class="contact-links">
    <span><svg viewBox="0 0 12 12"><rect x="0.5" y="2" width="11" height="8" fill="#f6b100"/><path d="M0.5 2.5l5.5 4 5.5-4" fill="none" stroke="#fff" stroke-width="1"/></svg>www.summitstonebuilders.com</span>
    <span><svg viewBox="0 0 12 12"><circle cx="6" cy="6" r="5.2" fill="none" stroke="#f6b100" stroke-width="1"/><ellipse cx="6" cy="6" rx="2.3" ry="5.2" fill="none" stroke="#f6b100" stroke-width="1"/><path d="M0.8 6h10.4" stroke="#f6b100" stroke-width="1"/></svg>info@summitstonebuilders.com</span>
  </div>

  <div class="estimate-band">
    <svg class="phone-icon" viewBox="0 0 22 22" aria-hidden="true">
      <rect width="22" height="22" rx="2" fill="#f6b100"/>
      <path d="M7 4.5c.6 0 1 .3 1.2.8l.9 2.3c.2.5 0 1-.4 1.3l-1 .7c.7 1.6 1.9 2.9 3.5 3.7l.8-1c.3-.4.9-.5 1.3-.3l2.2 1c.5.2.7.7.6 1.2l-.3 1.5c-.1.5-.6.9-1.1.9C9.4 16.3 5.7 12.6 5.5 6.4c0-.5.3-1 .8-1.1z" fill="#15304a"/>
    </svg>
    <span class="phone">555-014-2280</span>
    <span class="cta">FOR FREE ESTIMATE</span>
  </div>
</main>
</body>
</html>
```